Business card and (possibly) logo

Hi - we need a new business card.
We have an existing logo that we quite like but we are open to options.
We are an architectural firm - we specialize in upmarket residential work and apartment blocks.
We are chasing a business card at present but also want to extensively update our website going forward to attract a much higher level of client / investor / developer.
Our current logo is black, grey and yellow and based on the sun/moon temples in Mexico.
We are open to variations.
We want to communicate professionalism, trust, quality.
Our website is www.halvorenarchitects.com.au - but note as above - we want to change the website as well to be a lot 'classier' and to appeal to a higher end market.

thanks

Target Market(s)

We are an architect firm - our target market is Developers and builders of high end houses and luxury apartment blocks. Also private home owners wanting to build excellent expensive houses. (ideally over $1m budgets)

Industry/Entity Type

Residential

Requirements
Must have
• Logo
Contact details;
Name
phone, mobile, email, web

```html
<!DOCTYPE html>
<html lang="en">
<head>
<meta charset="utf-8">
<title>Halvoren Architects – Business Card</title>
<link href="https://fonts.googleapis.com/css2?family=Cabin:wght@400;600;700&display=swap" rel="stylesheet">
<style>
  :root {
    --backdrop: #d9d9d9;
    --card: #ffffff;
    --ink-grey: #7a7a7a;
    --ink-dark: #555555;
    --accent: #f0a30a;
    --band: #1c1c1c;
    --faint: #ececec;
    --social: #8fa3b8;
  }
  * { box-sizing: border-box; margin: 0; padding: 0; }
  html, body { width: 1200px; height: 787px; overflow: hidden; }
  body {
    background: radial-gradient(ellipse at 50% 45%, #ededed 0%, var(--backdrop) 75%);
    font-family: "Cabin", "Calibri", sans-serif;
    color: var(--ink-grey);
    position: relative;
  }
  .card {
    position: absolute;
    top: 243px;
    width: 520px;
    height: 300px;
    background: var(--card);
    box-shadow: 0 6px 18px rgba(0,0,0,0.18);
    overflow: hidden;
  }
  .card::after {
    content: "";
    position: absolute;
    left: 0; right: 0; bottom: 0;
    height: 16px;
    background: var(--band);
  }
  .card--front { left: 60px; }
  .card--back { left: 620px; }

  .wordmark {
    font-weight: 600;
    color: var(--ink-grey);
    letter-spacing: 0.5px;
    white-space: nowrap;
  }
  .card--front .wordmark {
    position: absolute;
    top: 104px;
    left: 0; right: 0;
    text-align: center;
    font-size: 32px;
  }
  .brand-dot {
    display: inline-block;
    width: 14px; height: 14px;
    border-radius: 50%;
    background: var(--accent);
    margin-right: 10px;
    vertical-align: 3px;
  }

  .call {
    position: absolute;
    left: 28px; bottom: 34px;
  }
  .call__label { font-size: 15px; color: var(--ink-grey); }
  .call__number { font-size: 22px; font-weight: 700; color: var(--accent); margin-top: 2px; }

  .social {
    position: absolute;
    right: 28px; bottom: 38px;
    text-align: left;
  }
  .social__label { font-size: 13px; color: var(--ink-grey); margin-bottom: 4px; }
  .social__icons { display: flex; gap: 5px; }
  .social__icons span {
    width: 30px; height: 30px;
    border-radius: 5px;
    background: var(--social);
  }

  .person {
    position: absolute;
    left: 34px; top: 34px;
    text-align: right;
    width: 120px;
  }
  .person__name { font-size: 14px; font-weight: 700; color: var(--accent); letter-spacing: 0.4px; }
  .person__role { font-size: 14px; color: var(--ink-grey); margin-top: 2px; }

  .contacts {
    position: absolute;
    left: 178px; top: 34px;
    list-style: none;
    font-size: 14px;
    color: var(--ink-dark);
  }
  .contacts li { display: flex; align-items: flex-start; line-height: 18px; }
  .contacts li.gap { margin-top: 16px; }
  .contacts svg { width: 13px; height: 13px; margin-top: 2px; flex: none; }
  .contacts .sep { color: #aaa; margin: 0 7px 0 6px; }

  .mark-space {
    position: absolute;
    left: -40px; bottom: -60px;
    width: 230px; height: 230px;
    border-radius: 50%;
    background: var(--faint);
  }
  .card--back .wordmark {
    position: absolute;
    right: 34px; bottom: 52px;
    font-size: 25px;
  }
</style>
</head>
<body>

<section class="card card--front" aria-label="Card front">
  <div class="wordmark"><span class="brand-dot"></span>HALVOREN ARCHITECTS</div>

  <div class="call">
    <p class="call__label">Call us now on:</p>
    <p class="call__number">1300 555 412</p>
  </div>

  <div class="social">
    <p class="social__label">Find us on:</p>
    <div class="social__icons" aria-label="Social media links">
      <span></span><span></span><span></span><span></span>
    </div>
  </div>
</section>

<section class="card card--back" aria-label="Card back">
  <div class="mark-space" role="img" aria-label="Faint brand mark area"></div>

  <div class="person">
    <p class="person__name">FIRST NAME</p>
    <p class="person__role">Designation</p>
  </div>

  <ul class="contacts">
    <li>
      <svg viewBox="0 0 16 16" aria-hidden="true"><path d="M4 1h3l1 4-2 1c1 2 2 3 4 4l1-2 4 1v3c0 1-1 2-2 2C7 14 2 9 2 3c0-1 1-2 2-2z" fill="none" stroke="#888" stroke-width="1.3"/></svg>
      <span class="sep">|</span>0400 555 182
    </li>
    <li>
      <svg viewBox="0 0 16 16" aria-hidden="true"><rect x="1.5" y="3.5" width="13" height="9" fill="none" stroke="#888" stroke-width="1.3"/><path d="M1.5 3.5 8 9l6.5-5.5" fill="none" stroke="#888" stroke-width="1.3"/></svg>
      <span class="sep">|</span>firstname@halvorenarchitects.com.au
    </li>
    <li>
      <svg viewBox="0 0 16 16" aria-hidden="true"><circle cx="8" cy="8" r="6.5" fill="none" stroke="#777" stroke-width="1.4"/><path d="M1.5 8h13M8 1.5c-3 3-3 10 0 13M8 1.5c3 3 3 10 0 13" fill="none" stroke="#777" stroke-width="1.1"/></svg>
      <span class="sep">|</span>www.halvorenarchitects.com.au
    </li>
    <li class="gap">
      <svg viewBox="0 0 16 16" aria-hidden="true"><rect x="1.5" y="5" width="13" height="8" fill="none" stroke="#888" stroke-width="1.3"/><rect x="4" y="2" width="8" height="3" fill="none" stroke="#888" stroke-width="1.2"/></svg>
      <span class="sep">|</span>880 Coralind WA 6158
    </li>
    <li>
      <svg viewBox="0 0 16 16" aria-hidden="true"><rect x="3" y="1.5" width="10" height="13" fill="none" stroke="#777" stroke-width="1.3"/><path d="M5.5 4h1.5M9 4h1.5M5.5 7h1.5M9 7h1.5M5.5 10h1.5M9 10h1.5" stroke="#777" stroke-width="1.3"/></svg>
      <span class="sep">|</span><span>Suite 7, 42 - 48 Coralind<br>Beach Road, Coralind, WA 6158</span>
    </li>
  </ul>

  <div class="wordmark">HALVOREN ARCHITECTS</div>
</section>

</body>
</html>
```